RWT Fittings Ltd Business Cards

We need a business card with our business logo. We provide window and door installations on high-rises in west coast British Colombia, Canada.

I would like my business information and details on one side of the card, and the other side the company name with logo

Target Market(s)

General Contractors

Industry/Entity Type

Construction

Contact Information for Business Card

one side i want my company name and logo in the dark theme logo that i provided

Requirements
Must have
• Marco Peltieri, 16045518293, RWTFittings@mailbox-demo.com, 1407-5194 Linden Row Burnaby BC, V5H 2K9, Owner & Manager

```html
<!DOCTYPE html>
<html lang="en">
<head>
<meta charset="UTF-8">
<title>RWT Fittings Ltd – Business Cards</title>
<link rel="stylesheet" href="https://fonts.googleapis.com/css2?family=Montserrat:wght@600;700;800&family=Roboto:wght@400;500&display=swap">
<style>
  :root {
    --stage: #232323;
    --card: #1f2024;
    --card-layer-1: #26272c;
    --card-layer-2: #1b1c20;
    --accent: #1fa6e0;
    --silver: #b9bcc0;
    --grey-name: #a9abae;
    --ink-light: #f2f3f5;
  }
  * { box-sizing: border-box; margin: 0; padding: 0; }
  html, body {
    width: 1200px; height: 780px; overflow: hidden;
    background: var(--stage);
  }
  .stage {
    position: relative; width: 1200px; height: 780px;
    display: flex; justify-content: center; align-items: center; gap: 80px;
  }
  .card {
    position: relative; width: 320px; height: 560px;
    background: var(--card); border-radius: 18px; overflow: hidden;
    box-shadow: 0 18px 40px rgba(0,0,0,.55);
  }

  /* Front: company name */
  .front-brand {
    position: absolute; left: 50%; top: 50%;
    transform: translate(-50%, -50%) rotate(-90deg);
    display: flex; align-items: center; gap: 18px; white-space: nowrap;
  }
  .front-brand__square {
    width: 34px; height: 34px; background: var(--accent);
  }
  .front-brand__name {
    font-family: "Montserrat", sans-serif; font-weight: 800;
    font-size: 38px; letter-spacing: 1px; color: var(--silver);
  }

  /* Back: contact details */
  .back-layers { position: absolute; inset: 0; }
  .back-brand {
    position: absolute; top: 52px; left: 0; right: 0;
    display: flex; justify-content: center; align-items: center; gap: 10px;
  }
  .back-brand__square { width: 18px; height: 18px; background: var(--accent); }
  .back-brand__name {
    font-family: "Montserrat", sans-serif; font-weight: 800;
    font-size: 22px; color: var(--accent); letter-spacing: .5px;
  }
  .contact {
    position: absolute; top: 250px; left: 0; right: 0; text-align: center;
    font-family: "Roboto", sans-serif; color: var(--ink-light);
  }
  .contact__name {
    font-family: "Montserrat", sans-serif; font-weight: 800; font-size: 27px; line-height: 1.1;
  }
  .contact__first { color: var(--accent); }
  .contact__last { color: var(--grey-name); }
  .contact__role {
    font-family: "Montserrat", sans-serif; font-weight: 700; font-size: 12px; margin-top: 4px;
  }
  .contact__icons { display: flex; justify-content: center; gap: 10px; margin: 14px 0 10px; }
  .icon-badge {
    width: 24px; height: 24px; border-radius: 50%; background: var(--accent);
    display: flex; align-items: center; justify-content: center;
  }
  .contact__line { font-size: 13px; line-height: 1.55; }
  .address {
    position: absolute; top: 458px; left: 0; right: 0; text-align: center;
    font-family: "Roboto", sans-serif; color: var(--ink-light); font-size: 13px; line-height: 1.45;
  }
  .address .icon-badge { margin: 0 auto 8px; }
</style>
</head>
<body>
<main class="stage">

  <section class="card card--front" aria-label="Card front">
    <div class="front-brand">
      <span class="front-brand__square"></span>
      <span class="front-brand__name">RWT Fittings Ltd</span>
    </div>
  </section>

  <section class="card card--back" aria-label="Card back">
    <svg class="back-layers" width="320" height="560" viewBox="0 0 320 560" aria-hidden="true">
      <path d="M0 372 Q150 395 320 300 L320 560 L0 560 Z" fill="var(--card-layer-1)"/>
      <path d="M0 372 Q150 395 320 300" fill="none" stroke="rgba(0,0,0,.5)" stroke-width="3"/>
      <path d="M60 560 Q150 420 320 385 L320 560 Z" fill="var(--card-layer-2)"/>
    </svg>

    <div class="back-brand">
      <span class="back-brand__square"></span>
      <span class="back-brand__name">RWT Fittings Ltd</span>
    </div>

    <div class="contact">
      <p class="contact__name"><span class="contact__first">Marco</span> <span class="contact__last">Peltieri</span></p>
      <p class="contact__role">Owner &amp; Manager</p>
      <div class="contact__icons">
        <span class="icon-badge" aria-label="Phone">
          <svg width="14" height="14" viewBox="0 0 24 24"><path fill="#fff" d="M6.6 10.8a15 15 0 0 0 6.6 6.6l2.2-2.2a1 1 0 0 1 1-.25 11.4 11.4 0 0 0 3.6.57 1 1 0 0 1 1 1V20a1 1 0 0 1-1 1A17 17 0 0 1 3 4a1 1 0 0 1 1-1h3.5a1 1 0 0 1 1 1c0 1.25.2 2.45.57 3.57a1 1 0 0 1-.25 1z"/></svg>
        </span>
        <span class="icon-badge" aria-label="Email">
          <svg width="14" height="14" viewBox="0 0 24 24"><path fill="#fff" d="M3 5h18a1 1 0 0 1 1 1v12a1 1 0 0 1-1 1H3a1 1 0 0 1-1-1V6a1 1 0 0 1 1-1zm9 7.2L4 7.5V8l8 5 8-5v-.5z"/></svg>
        </span>
      </div>
      <p class="contact__line">1604 551 8293</p>
      <p class="contact__line">RWTFittings@mailbox-demo.com</p>
    </div>

    <div class="address">
      <span class="icon-badge" aria-label="Location">
        <svg width="14" height="14" viewBox="0 0 24 24"><path fill="#fff" d="M12 2a7 7 0 0 0-7 7c0 5 7 13 7 13s7-8 7-13a7 7 0 0 0-7-7zm0 9.5A2.5 2.5 0 1 1 12 6.5a2.5 2.5 0 0 1 0 5z"/></svg>
      </span>
      <p>1407-5194 Linden Row</p>
      <p>Burnaby BC, V5H 2K9</p>
    </div>
  </section>

</main>
</body>
</html>
```